indépendant en tant que Massothérapeute et Préparateur Mental, j'ai besoin de ...

Massothérapeute et préparateur mental indépendant, je recherche une carte de visite sobre et dynamique, sans images liées au massage ou à la préparation mentale mais intégrant mon logo. Les couleurs que j'aime bien sont : Blanc, gris, anthracite, noir et jaune

Contact Information for Business Card

carte de préférence Horizontale
neutre qui puisse toucher le deux domaines Massothérapie et préparation mentale

Requirements
Must have
• mon projet doit intégrer au recto:
LOGO
Loïc Bardèze
078 513 26 48
info@loicbardeze.ch
et éventuellement www.loicbardeze.ch

et au verso les deux adresses:

Chemin des Ormilles 7B
1400 Yverdon-les-Bains

Route de la Gravière 9
1700 Fribourg

Should not have
• mon projet ne doit pas contenir d'image en liens avec le massage ni la préparation mentale.

```html
<!DOCTYPE html>
<html lang="fr">
<head>
<meta charset="utf-8">
<title>Loïc Bardèze – Carte de visite</title>
<link href="https://fonts.googleapis.com/css2?family=Raleway:wght@300;400;600&display=swap" rel="stylesheet">
<style>
  :root {
    --backdrop: #d9d9d9;
    --card: #222222;
    --card-edge: #2c2c2c;
    --ink-light: #c9c9c9;
    --ink-dim: #8a8a8a;
    --gloss: #0c0c0c;
    --silver: #9a9a9a;
  }
  * { box-sizing: border-box; margin: 0; padding: 0; }
  html, body { width: 1200px; height: 800px; overflow: hidden; }
  body {
    background: var(--backdrop);
    font-family: "Raleway", sans-serif;
    display: flex;
    align-items: center;
    justify-content: center;
    gap: 56px;
  }
  .card {
    width: 520px;
    height: 336px;
    background: var(--card);
    border-radius: 22px;
    position: relative;
    box-shadow: inset 0 0 0 1px var(--card-edge);
  }

  /* Contact side */
  .card--contact .contact-top {
    position: absolute;
    left: 0; right: 0; top: 92px;
    display: flex;
    align-items: center;
    justify-content: center;
    gap: 26px;
  }
  .holder-name {
    font-weight: 300;
    font-size: 21px;
    letter-spacing: 0.12em;
    text-transform: uppercase;
    color: var(--ink-light);
  }
  .divider {
    width: 1px;
    height: 62px;
    background: var(--ink-dim);
  }
  .contact-list, .address-list { list-style: none; }
  .contact-list li, .address-list li {
    display: flex;
    align-items: center;
    gap: 9px;
    color: var(--ink-light);
    font-weight: 400;
    line-height: 1.35;
  }
  .contact-list li { font-size: 13.5px; }
  .icon { width: 11px; height: 11px; flex: none; fill: var(--ink-light); }
  .address-list {
    position: absolute;
    left: 92px; top: 218px;
  }
  .address-list li { font-size: 14.5px; line-height: 1.5; }

  /* Brand side */
  .card--brand .brand {
    position: absolute;
    left: 72px; top: 138px;
    display: flex;
    align-items: center;
    gap: 16px;
  }
  .brand-mark {
    width: 46px; height: 46px;
    background: var(--silver);
    border-radius: 4px;
  }
  .brand-name {
    font-weight: 600;
    font-size: 30px;
    color: var(--gloss);
    line-height: 1;
  }
  .brand-role {
    margin-top: 5px;
    font-weight: 600;
    font-size: 10.5px;
    letter-spacing: 0.14em;
    text-transform: uppercase;
    color: var(--gloss);
  }
</style>
</head>
<body>

  <section class="card card--contact" aria-label="Verso : coordonnées">
    <div class="contact-top">
      <p class="holder-name">Loïc Bardèze</p>
      <span class="divider"></span>
      <ul class="contact-list">
        <li>
          <svg class="icon" viewBox="0 0 12 12"><path d="M2.5 1 L4.5 1 L5.2 3.4 L4 4.4 Q5 6.8 7.6 8 L8.6 6.8 L11 7.5 L11 9.5 Q10.5 11 9 11 Q1 10 1 3 Q1 1.5 2.5 1 Z"/></svg>
          078 513 26 48
        </li>
        <li>
          <svg class="icon" viewBox="0 0 12 12"><path d="M1 2.5 H11 V9.5 H1 Z M1.6 3.2 L6 6.6 L10.4 3.2" fill="none" stroke="#c9c9c9" stroke-width="1.2"/></svg>
          info@loicbardeze.ch
        </li>
        <li>
          <svg class="icon" viewBox="0 0 12 12"><circle cx="6" cy="6" r="5" fill="none" stroke="#c9c9c9" stroke-width="1.2"/><path d="M1 6 H11 M6 1 Q3 6 6 11 M6 1 Q9 6 6 11" fill="none" stroke="#c9c9c9" stroke-width="0.9"/></svg>
          www.loicbardeze.ch
        </li>
      </ul>
    </div>
    <ul class="address-list">
      <li>
        <svg class="icon" viewBox="0 0 12 12"><path d="M6 0.5 Q10 0.5 10 4.5 Q10 7 6 11.5 Q2 7 2 4.5 Q2 0.5 6 0.5 Z M6 3 A1.5 1.5 0 1 0 6 6 A1.5 1.5 0 1 0 6 3 Z" fill-rule="evenodd"/></svg>
        Chemin des Ormilles 7B, 1400 Yverdon-les-Bains
      </li>
      <li>
        <svg class="icon" viewBox="0 0 12 12"><path d="M6 0.5 Q10 0.5 10 4.5 Q10 7 6 11.5 Q2 7 2 4.5 Q2 0.5 6 0.5 Z M6 3 A1.5 1.5 0 1 0 6 6 A1.5 1.5 0 1 0 6 3 Z" fill-rule="evenodd"/></svg>
        Route de la Gravière 9, 1700 Fribourg
      </li>
    </ul>
  </section>

  <section class="card card--brand" aria-label="Recto : identité">
    <div class="brand">
      <span class="brand-mark"></span>
      <div>
        <p class="brand-name">Loïc Bardèze</p>
        <p class="brand-role">Massothérapeute / Préparateur Mental</p>
      </div>
    </div>
  </section>

</body>
</html>
```